An A5, double sided, ticklist

This is for a game at our Pilates + Yoga Studio. A list of things that they need to tick off over the month to earn different points. There are different point categories - a 1 point, 2 point, 5 point and 10 point category.

Under each category is a task they have to complete. ie Under 1 point is: * attend a reformer class * attend a yoga class * attend a sculpt class * follow the studio on Pixelgram

Under 2 points is
* do two classes in a row * do a class with a teacher you haven't had in the last month * write a review for your class on Pulsefolio

Under 3 points is:
* bring a friend or family member to class (not a current member) *wear a piece of studio merch to class * write a findora review

Under 5 points is:
* wear a costume to class and keep it on for the class * have a friend/family member register at the studio as a member this month

Beside each line of a task to complete can there by 3 tick boxes please (ie they can achieve each task 3 times). And then at the end of those tick boxes is space for a total (ie 3 x 2 points = 6).

At the end of each section is their total number of points for that section, and then at the end of the card is the grand total.

It is REQUIRED that this design is made in Canva so that I have access to the design once it's completed so I can add in extra category lines as I think of them.

The caption for the card is Bright Meadow Studio Birthday 2026!

Colours to use are yellow, white + orange. You can see our website here - brightmeadowstudio.nz or our Pixelgram @bright_meadowstudio to get a feel for the studio + the colours we use!

Thank you!

```html
<!DOCTYPE html>
<html lang="en">
<head>
<meta charset="utf-8">
<title>Bright Meadow Studio Birthday 2026 – Ticklist</title>
<link rel="stylesheet" href="https://fonts.googleapis.com/css2?family=Abril+Fatface&family=Poppins:wght@400;500;600;700;800&display=swap">
<style>
  :root{
    --page:#f1f1f1;
    --cream:#fff8ec;
    --cream-deep:#fce8c6;
    --orange:#e58535;
    --orange-soft:#f2b27a;
    --yellow:#f0bb57;
    --gold:#ffd23a;
    --rust:#b75c3c;
    --ink:#454545;
    --ink-dark:#3a3a3a;
    --white:#ffffff;
  }
  *{box-sizing:border-box;margin:0;padding:0}
  html,body{width:1200px;height:951px;overflow:hidden}
  body{background:var(--page);font-family:"Poppins",sans-serif;color:var(--ink);position:relative}

  .card{position:absolute;top:137px;width:478px;height:678px;overflow:hidden;
    background:radial-gradient(ellipse at 50% 45%,var(--white) 0%,var(--cream) 45%,var(--cream-deep) 100%)}
  .card--front{left:97px}
  .card--back{left:626px}
  .card-decor{position:absolute;inset:0;width:478px;height:678px}

  /* title lockup */
  .title{position:absolute;left:0;width:100%;text-align:center;font-family:"Abril Fatface",serif;line-height:1}
  .title span{display:block}
  .title-bright{color:var(--ink)}
  .title-meadow{color:var(--orange)}
  .title-studio{color:var(--ink);display:flex !important;align-items:center;justify-content:center;gap:10px}
  .title-studio::before,.title-studio::after{content:"";height:2px;background:var(--ink);display:block}
  .title-birthday{color:var(--ink)}
  .title-year{color:var(--orange)}

  .card--front .title{top:205px}
  .card--front .title-bright{font-size:50px;margin-left:70px}
  .card--front .title-meadow{font-size:62px;margin-top:-2px}
  .card--front .title-studio{font-size:24px;margin-top:8px}
  .card--front .title-studio::before,.card--front .title-studio::after{width:60px}
  .card--front .title-birthday{font-size:68px;margin-top:2px}
  .card--front .title-year{font-size:50px;margin-top:2px}

  .card--back .title{top:22px}
  .card--back .title-bright{font-size:24px;margin-left:30px}
  .card--back .title-meadow{font-size:32px}
  .card--back .title-studio{font-size:13px;margin-top:3px}
  .card--back .title-studio::before,.card--back .title-studio::after{width:34px;height:1.5px}
  .card--back .title-birthday{font-size:36px}
  .card--back .title-year{font-size:26px;margin-top:1px}

  .studio-name{position:absolute;top:112px;left:0;width:100%;text-align:center;
    font-family:"Poppins",sans-serif;font-weight:600;color:var(--orange);font-size:21px;line-height:1.15;letter-spacing:.5px}

  .handle{position:absolute;left:128px;top:481px;width:246px;height:36px;transform:rotate(-3deg);
    background:var(--orange);border-radius:18px;display:flex;align-items:center;padding-left:8px;gap:10px}
  .handle-dot{width:36px;height:36px;border-radius:50%;background:var(--rust);margin-left:-16px;flex:none}
  .handle-text{color:var(--white);font-weight:700;font-size:16px}
  .website{position:absolute;left:0;width:100%;top:526px;text-align:center;transform:rotate(-2deg);
    font-weight:700;font-size:14px;color:var(--ink-dark);letter-spacing:.6px}

  .yoga-figure{position:absolute;border-radius:50%;
    background:radial-gradient(ellipse,rgba(229,133,53,.28),rgba(229,133,53,0) 70%)}
  .yoga-figure--left{left:40px;top:80px;width:80px;height:64px}
  .yoga-figure--right{left:380px;top:120px;width:52px;height:40px}

  /* tiers */
  .tier{position:absolute;left:45px;width:385px;height:110px;border:1px solid var(--orange-soft);background:rgba(255,246,228,.75)}
  .tier--1{top:166px}
  .tier--2{top:280px}
  .tier--3{top:395px}
  .tier--5{top:510px}
  .tier-head{position:absolute;top:1px;left:16px;display:flex;height:19px}
  .tier-stars{width:84px;background:var(--orange);display:flex;align-items:center;gap:1px;padding-left:6px}
  .tier-label{width:71px;background:var(--ink-dark);color:var(--white);font-weight:700;font-size:12px;
    display:flex;align-items:center;justify-content:center;gap:3px}
  .tier-label b{color:var(--gold);font-weight:700}
  .star{width:13px;height:13px;flex:none}

  .tasks{list-style:none}
  .task{position:absolute;left:16px;right:17px;display:flex;align-items:flex-start;
    font-size:8.6px;line-height:12px;color:var(--ink-dark)}
  .task-bullet{width:5px;height:5px;border-radius:50%;background:var(--orange);margin:3.5px 5px 0 0;flex:none}
  .task-text{width:216px;padding-right:10px;flex:none}
  .ticks{display:flex;gap:6px;flex:none}
  .tick{width:12px;height:11px;border:1px solid var(--orange-soft);background:var(--white)}
  .task-eq{margin:0 4px 0 9px;font-size:8px;line-height:11px}
  .task-total{flex:1;border-bottom:1px solid #bbb;height:9px}

  .tier-total{position:absolute;left:16px;bottom:0;width:94px;height:19px;background:var(--yellow);
    color:var(--white);font-size:8.5px;font-weight:600;display:flex;align-items:center;padding-left:12px;letter-spacing:.3px}
  .tier-total-box{position:absolute;right:17px;bottom:1px;width:120px;height:20px;background:var(--white);border:1px solid #f3dcc0}

  .grand-total{position:absolute;left:46px;top:624px;width:384px;height:28px;display:flex}
  .grand-total-label{width:246px;background:var(--ink-dark);display:flex;align-items:center;justify-content:center;gap:6px;
    color:var(--white);font-weight:800;font-size:16.5px;letter-spacing:.3px}
  .grand-total-label .star{width:14px;height:14px}
  .grand-total-stars{display:flex;gap:1px}
  .grand-total-box{flex:1;background:var(--white);border:1px solid #f3dcc0}
</style>
</head>
<body>

<svg width="0" height="0" style="position:absolute" aria-hidden="true">
  <defs>
    <symbol id="star-badge" viewBox="0 0 20 20">
      <circle cx="10" cy="10" r="9.5" fill="#f39b2a" stroke="#fff1c4" stroke-width="1"/>
      <polygon points="10,3.5 11.9,7.8 16.4,8.1 13,11.1 14,15.6 10,13.2 6,15.6 7,11.1 3.6,8.1 8.1,7.8" fill="#ffd23a"/>
    </symbol>
  </defs>
</svg>

<!-- Front side -->
<section class="card card--front" aria-label="Front of ticklist">
  <svg class="card-decor" viewBox="0 0 478 678" aria-hidden="true">
    <path d="M40 0 H290 C270 30 230 55 180 52 C130 50 80 40 40 0Z" fill="var(--yellow)"/>
    <path d="M0 0 H200 C185 45 150 80 110 105 C75 125 40 150 0 165Z" fill="var(--orange)"/>
    <path d="M310 0 H478 V72 C440 82 405 66 390 45 C375 28 330 40 310 0Z" fill="var(--rust)"/>
    <path d="M478 75 C455 100 440 130 455 160 C465 180 470 190 478 195" fill="none" stroke="var(--orange)" stroke-width="10"/>
    <path d="M478 465 C440 500 410 540 430 590" fill="none" stroke="var(--orange)" stroke-width="14"/>
    <path d="M0 600 C90 570 170 600 250 640 C320 670 400 640 478 645 V678 H0Z" fill="var(--orange)"/>
    <path d="M230 678 C270 620 360 570 478 560 V678Z" fill="var(--yellow)"/>
    <path d="M0 565 C80 545 150 560 220 600" fill="none" stroke="var(--ink)" stroke-width="1"/>
    <path d="M0 640 C60 625 130 640 200 678" fill="none" stroke="var(--white)" stroke-width="1.2" opacity=".7"/>
    <path d="M410 20 l3 8 8 3 -8 3 -3 8 -3 -8 -8 -3 8 -3z" fill="var(--white)"/>
  </svg>

  <div class="studio-name">Bright Meadow<br>Studio</div>

  <h1 class="title">
    <span class="title-bright">Bright</span>
    <span class="title-meadow">Meadow</span>
    <span class="title-studio">Studio</span>
    <span class="title-birthday">Birthday</span>
    <span class="title-year">2026</span>
  </h1>

  <div class="handle"><span class="handle-dot"></span><span class="handle-text">bright_meadowstudio</span></div>
  <p class="website">www.brightmeadowstudio.nz</p>
</section>

<!-- Back side -->
<section class="card card--back" aria-label="Back of ticklist">
  <svg class="card-decor" viewBox="0 0 478 678" aria-hidden="true">
    <path d="M0 0 H150 C140 40 110 70 70 90 C40 105 20 115 0 130Z" fill="var(--orange)"/>
    <path d="M350 0 H478 V62 C445 70 420 55 410 38 C395 20 365 30 350 0Z" fill="var(--rust)"/>
    <path d="M478 62 C460 90 455 120 465 140" fill="none" stroke="var(--orange)" stroke-width="8"/>
    <path d="M0 600 C60 590 120 610 180 650 C200 664 215 672 230 678 H0Z" fill="var(--orange)"/>
    <path d="M240 678 C300 650 380 600 478 585 V678Z" fill="var(--yellow)"/>
    <path d="M440 15 l3 7 7 3 -7 3 -3 7 -3 -7 -7 -3 7 -3z" fill="var(--white)"/>
  </svg>

  <div class="yoga-figure yoga-figure--left" role="img" aria-label="Line drawing of a seated meditating figure"></div>
  <div class="yoga-figure yoga-figure--right" role="img" aria-label="Small line drawing of a seated meditating figure"></div>

  <h2 class="title">
    <span class="title-bright">Bright</span>
    <span class="title-meadow">Meadow</span>
    <span class="title-studio">Studio</span>
    <span class="title-birthday">Birthday</span>
    <span class="title-year">2026</span>
  </h2>

  <div class="tier tier--1">
    <div class="tier-head">
      <div class="tier-stars"><svg class="star"><use href="#star-badge"/></svg></div>
      <div class="tier-label"><b>01</b>POINT</div>
    </div>
    <ul class="tasks">
      <li class="task" style="top:30px"><span class="task-bullet"></span><span class="task-text">Attend a reformer class</span><span class="ticks"><i class="tick"></i><i class="tick"></i><i class="tick"></i></span><span class="task-eq">=</span><span class="task-total"></span></li>
      <li class="task" style="top:45px"><span class="task-bullet"></span><span class="task-text">Attend a yoga class</span><span class="ticks"><i class="tick"></i><i class="tick"></i><i class="tick"></i></span><span class="task-eq">=</span><span class="task-total"></span></li>
      <li class="task" style="top:60px"><span class="task-bullet"></span><span class="task-text">Attend a sculpt class</span><span class="ticks"><i class="tick"></i><i class="tick"></i><i class="tick"></i></span><span class="task-eq">=</span><span class="task-total"></span></li>
      <li class="task" style="top:75px"><span class="task-bullet"></span><span class="task-text">Follow the studio on Pixelgram</span><span class="ticks"><i class="tick"></i><i class="tick"></i><i class="tick"></i></span><span class="task-eq">=</span><span class="task-total"></span></li>
    </ul>
    <div class="tier-total">SECTION TOTAL</div>
    <div class="tier-total-box"></div>
  </div>

  <div class="tier tier--2">
    <div class="tier-head">
      <div class="tier-stars"><svg class="star"><use href="#star-badge"/></svg><svg class="star"><use href="#star-badge"/></svg></div>
      <div class="tier-label"><b>02</b>POINT</div>
    </div>
    <ul class="tasks">
      <li class="task" style="top:31px"><span class="task-bullet"></span><span class="task-text">Do two classes in a row</span><span class="ticks"><i class="tick"></i><i class="tick"></i><i class="tick"></i></span><span class="task-eq">=</span><span class="task-total"></span></li>
      <li class="task" style="top:47px"><span class="task-bullet"></span><span class="task-text">Do a class with a teacher you haven't had in the last month</span><span class="ticks"><i class="tick"></i><i class="tick"></i><i class="tick"></i></span><span class="task-eq">=</span><span class="task-total"></span></li>
      <li class="task" style="top:74px"><span class="task-bullet"></span><span class="task-text">Write a review for your class on Pulsefolio</span><span class="ticks"><i class="tick"></i><i class="tick"></i><i class="tick"></i></span><span class="task-eq">=</span><span class="task-total"></span></li>
    </ul>
    <div class="tier-total">SECTION TOTAL</div>
    <div class="tier-total-box"></div>
  </div>

  <div class="tier tier--3">
    <div class="tier-head">
      <div class="tier-stars"><svg class="star"><use href="#star-badge"/></svg><svg class="star"><use href="#star-badge"/></svg><svg class="star"><use href="#star-badge"/></svg></div>
      <div class="tier-label"><b>03</b>POINT</div>
    </div>
    <ul class="tasks">
      <li class="task" style="top:30px"><span class="task-bullet"></span><span class="task-text">Bring a friend or family member to class (not a current member)</span><span class="ticks"><i class="tick"></i><i class="tick"></i><i class="tick"></i></span><span class="task-eq">=</span><span class="task-total"></span></li>
      <li class="task" style="top:58px"><span class="task-bullet"></span><span class="task-text">Wear a piece of studio merch to class</span><span class="ticks"><i class="tick"></i><i class="tick"></i><i class="tick"></i></span><span class="task-eq">=</span><span class="task-total"></span></li>
      <li class="task" style="top:74px"><span class="task-bullet"></span><span class="task-text">Write a findora review</span><span class="ticks"><i class="tick"></i><i class="tick"></i><i class="tick"></i></span><span class="task-eq">=</span><span class="task-total"></span></li>
    </ul>
    <div class="tier-total">SECTION TOTAL</div>
    <div class="tier-total-box"></div>
  </div>

  <div class="tier tier--5">
    <div class="tier-head">
      <div class="tier-stars"><svg class="star"><use href="#star-badge"/></svg><svg class="star"><use href="#star-badge"/></svg><svg class="star"><use href="#star-badge"/></svg><svg class="star"><use href="#star-badge"/></svg><svg class="star"><use href="#star-badge"/></svg></div>
      <div class="tier-label"><b>05</b>POINT</div>
    </div>
    <ul class="tasks">
      <li class="task" style="top:30px"><span class="task-bullet"></span><span class="task-text">wear a costume to class and keep it on for the class</span><span class="ticks"><i class="tick"></i><i class="tick"></i><i class="tick"></i></span><span class="task-eq">=</span><span class="task-total"></span></li>
      <li class="task" style="top:59px"><span class="task-bullet"></span><span class="task-text">Have a friend/family member register at the studio as a member this month</span><span class="ticks"><i class="tick"></i><i class="tick"></i><i class="tick"></i></span><span class="task-eq">=</span><span class="task-total"></span></li>
    </ul>
    <div class="tier-total">SECTION TOTAL</div>
    <div class="tier-total-box"></div>
  </div>

  <div class="grand-total">
    <div class="grand-total-label">
      <span class="grand-total-stars"><svg class="star"><use href="#star-badge"/></svg><svg class="star"><use href="#star-badge"/></svg><svg class="star"><use href="#star-badge"/></svg></span>
      GRAND TOTAL
      <span class="grand-total-stars"><svg class="star"><use href="#star-badge"/></svg><svg class="star"><use href="#star-badge"/></svg><svg class="star"><use href="#star-badge"/></svg></span>
    </div>
    <div class="grand-total-box"></div>
  </div>
</section>

</body>
</html>
```